Laser Tattoo Removal Business Cards

We are looking for a professional business card design for a laser tattoo removal business. Ideally looking for a black business card design. The name of the business is Brightline Tattoo Removal. We place our cards at local tattoo shops so we ideally are looking for something trendy/edgy to draw both male and female clientele in.

Target Market(s)

Male/Female ages 18-60

Contact Information for Business Card

black background ideally.. hoping to stay within greys, whites and black

Font styles to use
Serif
Sans Serif

Colors
121212
a9a9a9
5c5c5c
f5f5f5
ffffff
7f7f7f
606060
848484
9d9d9d

Requirements
Must have
• Employee Info:
• Melissa Thornbury
• Chief Executive Offer
• m: 919.537.2846
• w: 919.362.4178
• f: 919.685.3907
• mthornbury@brightlinetattooremoval.example
• Address:
• 4615 Oakmere Pkwy, Suite 210
• Raleigh, NC 27654
• Website:
• www.brightlinetattooremoval.example
Nice to have
• Myabe business name on back or logo on back and employee info on the front

```html
<!DOCTYPE html>
<html lang="en">
<head>
<meta charset="utf-8">
<title>Brightline Tattoo Removal – Business Cards</title>
<link rel="stylesheet" href="https://fonts.googleapis.com/css2?family=Montserrat:wght@500&family=Roboto:wght@400;700&display=swap">
<style>
  :root {
    --ink: #121212;
    --card: #161616;
    --white: #ffffff;
    --paper: #f5f5f5;
    --silver: #a9a9a9;
    --grey: #7f7f7f;
    --grey-dark: #5c5c5c;
    --backdrop: #3a3330;
  }
  * { margin: 0; padding: 0; box-sizing: border-box; }
  html, body { width: 1200px; height: 769px; overflow: hidden; }
  body {
    background: var(--backdrop);
    font-family: "Roboto", Arial, sans-serif;
    position: relative;
  }
  .card {
    position: absolute;
    top: 229px;
    width: 540px;
    height: 310px;
    background: var(--card);
    overflow: hidden;
    box-shadow: 0 12px 30px rgba(0,0,0,.45);
  }
  .card--front { left: 40px; }
  .card--back { left: 620px; }

  .band { position: absolute; inset: 0; }

  .wordmark {
    position: absolute;
    left: 0; right: 0;
    text-align: center;
    font-family: "Montserrat", Arial, sans-serif;
    font-weight: 500;
    color: var(--white);
    line-height: 1;
  }
  .wordmark__name { display: block; font-size: 34px; letter-spacing: 2px; }
  .wordmark__sub { display: block; font-size: 13px; letter-spacing: 4px; margin-top: 10px; }
  .card--front .wordmark { top: 58px; }
  .card--back .wordmark { top: 92px; color: var(--silver); }

  .person {
    position: absolute;
    top: 150px; left: 120px; right: 120px;
    text-align: center;
    color: var(--white);
    border-top: 1px solid var(--silver);
    border-bottom: 1px solid var(--silver);
    padding: 8px 0 7px;
  }
  .person__name { font-weight: 700; font-size: 17px; letter-spacing: .5px; }
  .person__title { font-size: 13px; margin-top: 2px; }

  .contact {
    position: absolute;
    top: 218px; left: 10px; right: 10px;
    list-style: none;
    text-align: center;
    color: var(--white);
    font-size: 12.5px;
    line-height: 20px;
  }
  .contact__item { display: inline-flex; align-items: center; gap: 4px; margin: 0 4px; white-space: nowrap; }
  .icon { width: 11px; height: 11px; fill: var(--white); }

  .website {
    position: absolute;
    top: 205px; left: 0; right: 0;
    text-align: center;
    color: var(--paper);
    font-size: 12px;
    letter-spacing: 2.5px;
  }
</style>
</head>
<body>

<section class="card card--front">
  <svg class="band" viewBox="0 0 540 310" aria-hidden="true">
    <polygon points="0,118 150,118 162,96 0,96" fill="var(--white)"/>
    <polygon points="378,58 390,36 540,36 540,58" fill="var(--white)"/>
  </svg>
  <div class="wordmark">
    <span class="wordmark__name">BRIGHTLINE</span>
    <span class="wordmark__sub">TATTOO REMOVAL</span>
  </div>
  <div class="person">
    <div class="person__name">MELISSA THORNBURY</div>
    <div class="person__title">Chief Executive Offer</div>
  </div>
  <ul class="contact">
    <li class="contact__item">
      <svg class="icon" viewBox="0 0 24 24"><path d="M6.6 10.8a15.1 15.1 0 0 0 6.6 6.6l2.2-2.2c.3-.3.7-.4 1-.2 1.1.4 2.3.6 3.6.6.6 0 1 .4 1 1V20c0 .6-.4 1-1 1A17 17 0 0 1 3 4c0-.6.4-1 1-1h3.5c.6 0 1 .4 1 1 0 1.3.2 2.5.6 3.6.1.3 0 .7-.2 1z"/></svg>
      919.362.4178
    </li>
    <li class="contact__item">
      <svg class="icon" viewBox="0 0 24 24"><path d="M7 1h10a2 2 0 0 1 2 2v18a2 2 0 0 1-2 2H7a2 2 0 0 1-2-2V3a2 2 0 0 1 2-2zm0 3v15h10V4z"/></svg>
      919.537.2846
    </li>
    <li class="contact__item">
      <svg class="icon" viewBox="0 0 24 24"><path d="M6 2h10v5H6zM3 8h18a1 1 0 0 1 1 1v8h-4v5H6v-5H2V9a1 1 0 0 1 1-1zm5 8v4h8v-4z"/></svg>
      919.685.3907
    </li>
    <li class="contact__item">
      <svg class="icon" viewBox="0 0 24 24"><path d="M2 5h20v14H2zm2 2v.5l8 5 8-5V7zm0 3v7h16v-7l-8 5z"/></svg>
      mthornbury@brightlinetattooremoval.example
    </li>
    <li class="contact__item">
      <svg class="icon" viewBox="0 0 24 24"><circle cx="12" cy="12" r="10"/></svg>
      www.brightlinetattooremoval.example
    </li>
    <li class="contact__item">4615 Oakmere Pkwy, Suite 210, Raleigh, NC 27654</li>
  </ul>
</section>

<section class="card card--back">
  <div class="wordmark">
    <span class="wordmark__name">BRIGHTLINE</span>
    <span class="wordmark__sub">TATTOO REMOVAL</span>
  </div>
  <div class="website">www.brightlinetattooremoval.example</div>
</section>

</body>
</html>
```